Velmori Sciences needs high end Label Design for a revolutionary new supplement

We at Velmori Sciences are looking for a brand new Label Design for a first of its kind product called Solvenna. It is the first supplement on the market that treats grief and heartbreak. This product is unisex for both men and woman. We want the New Label to look high end and luxurious using the brand colors which are gold and burgundy. Please feel free to use other colors such as black, white, or gray to go along with it or any other colors if you feel would be a great fit! Velmori Sciences is like the Tarnwick of the supplement world, coming out with new products that will challenge the way people treat different symptoms. To Recap:

1. Product Name: SOLVENNA - the font will play a big roll
2. The Label will be placed on an all white bottle
3. Some parts of the label will be printed with foil to make parts of the label shiny and more attractive. Please keep this in mind when designing.
4. Must use our Logo. I will attach a file of our logo and of the emblem as well. Feel free to use the emblem separately if you have a great idea for it. Please let us know if you need the Logo in a different file type.
5. This all natural herbal supplement in pill form is the first to treat grief and support someone with a broken heart. The consumers purchasing this product will be going through a hard and emotional time. This is a serious product.
6. The manufacturer has included some basic instructions regarding the dye line and file types. Please do your best to meet these. If you cannot meet the guidelines please submit art work anyways. If your design is chosen we will just have the manufacturer replicate the design.

The final label should portray Solvenna and Velmori Sciences as a luxurious brand and product which was made with cutting edge science leading the way with revolutionary ideas. We want customers to feel that the product is worth every penny, because it is. As soon as they receive the product and take one look at the label, I want them to think WOW I made the right choice buying this. I have attached some Label designs that we really liked for your review.

Please feel free to message me with any questions or if you need the Logo in a different file type. Thank you all.
Updates

Please send in more entries while we take a couple days to review, we are still looking for that one design we can work with. We are getting close, thank you all!

Target Market(s)

People going through grief and heartbreak.

Font styles to use
Sans Serif
Script
Other font styles liked:
• Any font that looks good, The font for the name SOLVENNA is very important and will brand it. We hated the font used in the label we received in our first label draft (attached so you can see)

Requirements
Must have
• Must have the company Logo that says the company name
• Must have the colors Gold and Burgundy
• Must have some areas that will be the shiny foil when label is printed.
• Must say "Dietary Supplement" somewhere near the bottom along with "90 Capsules"
• I have attached a Label someone designed for us but were not really happy with. I did like the font the "Dietary supplement" and "90 Capsules" had and also where it was placed. We absolutely HATED the font used for Solvenna.
• Must look at the label design we received from the manufacturer and take into consideration the room needed to write in the directions and all the symbols such as "made in america" and "KMT Facility" Don't worry about adding these in as they will put those in before printing but keep in mind they will be added to the Final Label along with the Supplement Facts.
Nice to have
• Would like to see other colors to go with gold and burgundy suck as black, white, or gray. I have attached some Label designs that I really liked for your reference.
Should not have
• Does not need to have any other legal language, that will be applied by the the manufacturer's graphics team.

```html
<!DOCTYPE html>
<html lang="en">
<head>
<meta charset="utf-8">
<title>Solvenna Label</title>
<link href="https://fonts.googleapis.com/css2?family=Audiowide&family=Quicksand:wght@500;600&display=swap" rel="stylesheet">
<style>
  :root {
    --backdrop: #eceae7;
    --label-ivory: #f8efdf;
    --gold-light: #f3dc9a;
    --gold: #c9a14a;
    --gold-deep: #8f6a22;
    --burgundy: #7d1426;
    --wine: #4a0a16;
    --black: #1b1416;
    --ink: #2a1c1f;
  }
  * { box-sizing: border-box; margin: 0; padding: 0; }
  html, body { width: 1200px; height: 1200px; overflow: hidden; }
  body {
    background: var(--backdrop);
    font-family: "Quicksand", sans-serif;
    position: relative;
  }
  .label {
    position: absolute;
    left: 50px;
    top: 290px;
    width: 1100px;
    height: 620px;
    background: var(--label-ivory);
    overflow: hidden;
    border-top: 4px solid var(--gold);
    border-bottom: 4px solid var(--gold);
  }
  .pattern { position: absolute; }
  .pattern--top-left {
    left: 0; top: 0;
    width: 300px; height: 250px;
    background: linear-gradient(135deg, var(--burgundy) 0%, var(--wine) 35%, var(--gold) 60%, var(--gold-light) 75%, var(--black) 100%);
    clip-path: polygon(0 0, 100% 0, 100% 45%, 40% 100%, 0 100%);
  }
  .pattern--bottom-right {
    right: 0; bottom: 0;
    width: 300px; height: 320px;
    background: linear-gradient(135deg, var(--gold-light) 0%, var(--gold) 25%, var(--burgundy) 55%, var(--black) 80%, var(--wine) 100%);
    clip-path: polygon(50% 0, 100% 0, 100% 100%, 0 100%, 0 45%);
  }
  .brand {
    position: absolute;
    left: 0; right: 0;
    top: 118px;
    text-align: center;
    color: var(--burgundy);
    font-weight: 600;
  }
  .brand__dot {
    display: block;
    width: 44px; height: 44px;
    margin: 0 auto 12px;
    border-radius: 50%;
    background: var(--burgundy);
  }
  .brand__name {
    font-size: 30px;
    letter-spacing: 3px;
    line-height: 1.15;
    text-transform: uppercase;
  }
  .product-name {
    position: absolute;
    left: 0; right: 0;
    top: 272px;
    text-align: center;
    font-family: "Audiowide", sans-serif;
    font-weight: 400;
    font-size: 80px;
    line-height: 1;
    letter-spacing: 6px;
    color: var(--gold);
    background: linear-gradient(180deg, var(--gold-light) 0%, var(--gold) 45%, var(--gold-deep) 100%);
    -webkit-background-clip: text;
    background-clip: text;
    -webkit-text-fill-color: transparent;
  }
  .descriptor {
    position: absolute;
    left: 0; right: 0;
    top: 400px;
    text-align: center;
    font-size: 26px;
    font-weight: 500;
    line-height: 1.4;
    color: var(--burgundy);
  }
  .count {
    position: absolute;
    left: 0; right: 0;
    top: 498px;
    text-align: center;
    color: var(--burgundy);
  }
  .count__number {
    display: inline-block;
    font-size: 62px;
    font-weight: 500;
    line-height: 1;
    position: relative;
  }
  .count__number::after {
    content: "";
    position: absolute;
    right: -34px; top: 20px;
    border-left: 22px solid var(--gold);
    border-top: 13px solid transparent;
    border-bottom: 13px solid transparent;
  }
  .count__unit {
    display: block;
    font-size: 20px;
    font-weight: 500;
  }
  .side-info {
    position: absolute;
    left: 24px;
    top: 380px;
    width: 200px;
    color: var(--ink);
    font-size: 13px;
    font-weight: 600;
  }
  .side-info__badge {
    display: block;
    width: 50px; height: 50px;
    border-radius: 50%;
    border: 3px solid var(--ink);
    margin-bottom: 30px;
  }
</style>
</head>
<body>
  <main class="label">
    <div class="pattern pattern--top-left" role="img" aria-label="Geometric triangle pattern in burgundy, wine, gold foil and black"></div>
    <div class="pattern pattern--bottom-right" role="img" aria-label="Geometric triangle pattern in gold foil, burgundy and black"></div>

    <div class="side-info">
      <span class="side-info__badge" role="img" aria-label="Dietary badge"></span>
      <p>Distributed by:<br>Velmori Sciences, LLC</p>
    </div>

    <div class="brand">
      <span class="brand__dot"></span>
      <p class="brand__name">Velmori<br>Sciences</p>
    </div>

    <h1 class="product-name">SOLVENNA</h1>

    <p class="descriptor">Dietary<br>Supplement</p>

    <div class="count">
      <span class="count__number">90</span>
      <span class="count__unit">Capsules</span>
    </div>
  </main>
</body>
</html>
```